New Business Card Design Project

I need a design for business cards, i am an electrical business called "Corvane Electrical and Communications" i need the cards to be double sided with the company logo on the back (attached) the front needs to say my company name, web site, email address, telephone number, and ABN number and electrical license number. I am open to different arrangements of the information but would like the background to be incorporating something electrical or something that looks smart. open to all additional ideas also.

The company colours are orange and grey see logo attached.

Business Name: Corvane Electrical and Communications
Website: corvaneelectricalandcomms.example.com.au
Email: brent@corvaneelectricalandcomms.example.com.au
Telephone(mobile): 0481209736
ABN: 71208349162
Lic No: 418273D

Target Market(s)

Business entities, Project Managers, Accounts, Clients

Industry/Entity Type

Electrician

Contact Information for Business Card

I need a design for business cards, i am an electrical business called "Corvane Electrical and Communications" i need the cards to be double sided with the company logo on the back (attached) the front needs to say my company name

Font styles to use
Serif
Sans Serif

Colors
f37122
5c5c5c

Requirements
Must have
• Must have the Logo on the back open to different ways of it being on the back but had in mind to keep it central but again open to other options
Nice to have
• A real modern cool background that is eye catching yet contemporary
Should not have
• No backgrounds of a light bulb or plug or anything like that

```html
<!DOCTYPE html>
<html lang="en">
<head>
<meta charset="utf-8">
<title>Corvane Electrical and Communications – Business Cards</title>
<link rel="stylesheet" href="https://fonts.googleapis.com/css2?family=Arimo:wght@400;700&display=swap">
<style>
  :root {
    --orange: #f5a515;
    --orange-deep: #f39c12;
    --grey-dark: #4a4a4c;
    --grey-mid: #5c5c5c;
    --grey-text: #5a5a5a;
    --grey-soft: #9a9a9a;
    --white: #ffffff;
    --paper: #f4f4f4;
    --backdrop: #d9d9d9;
  }
  * { box-sizing: border-box; margin: 0; padding: 0; }
  html, body {
    width: 1200px; height: 950px; overflow: hidden;
    background: var(--backdrop);
    font-family: "Arimo", Arial, sans-serif;
  }
  .sheet {
    width: 1200px; height: 950px;
    display: flex; flex-direction: column; align-items: center; justify-content: center;
    gap: 50px;
  }
  .card {
    width: 700px; height: 400px; position: relative; overflow: hidden;
    border-radius: 4px;
    box-shadow: 0 10px 30px rgba(0,0,0,.25);
  }

  /* Back side */
  .card--back {
    background: linear-gradient(135deg, var(--grey-mid) 0%, var(--grey-dark) 100%);
  }
  .card--back .brand {
    position: absolute; left: 0; right: 0; top: 130px;
    display: flex; flex-direction: column; align-items: center; gap: 8px;
  }
  .card--back .website {
    position: absolute; right: 44px; bottom: 34px;
    color: var(--grey-soft); font-size: 17px; letter-spacing: .5px;
  }

  /* Brand wordmark */
  .brand { color: var(--white); font-weight: 700; }
  .brand__row { display: flex; align-items: center; gap: 14px; }
  .brand__dot { width: 18px; height: 18px; border-radius: 50%; background: var(--orange); }
  .brand__name { font-size: 64px; letter-spacing: 2px; line-height: 1; }
  .brand__sub { font-size: 15px; letter-spacing: 2.5px; text-transform: uppercase; }

  /* Front side */
  .card--front { background: var(--paper); }
  .front__top {
    position: absolute; left: 0; top: 0; width: 100%; height: 220px;
    background: linear-gradient(135deg, var(--grey-mid) 0%, var(--grey-dark) 100%);
  }
  .front__top .brand {
    position: absolute; left: 0; right: 0; top: 62px;
    display: flex; flex-direction: column; align-items: center; gap: 8px;
  }
  .front__band {
    position: absolute; left: 0; top: 220px; width: 100%; height: 80px;
    background: linear-gradient(90deg, var(--orange-deep), var(--orange));
    display: flex; flex-direction: column; align-items: center; justify-content: center;
    color: var(--white);
  }
  .person__name { font-size: 24px; font-weight: 700; letter-spacing: 1px; }
  .person__title { font-size: 17px; letter-spacing: 1px; margin-top: 3px; }
  .contacts {
    position: absolute; left: 0; right: 0; top: 300px; height: 100px;
    display: flex; flex-direction: column; align-items: center; justify-content: center; gap: 7px;
    color: var(--grey-text); font-size: 15px;
  }
  .contacts__row { display: flex; align-items: center; gap: 18px; }
  .contact { display: flex; align-items: center; gap: 6px; }
  .contact svg { width: 15px; height: 15px; fill: var(--orange); }
</style>
</head>
<body>
<main class="sheet">

  <section class="card card--back" aria-label="Card back">
    <div class="brand">
      <div class="brand__row">
        <span class="brand__dot"></span>
        <span class="brand__name">CORVANE</span>
      </div>
      <span class="brand__sub">Electrical and Communications</span>
    </div>
    <p class="website">corvaneelectricalandcomms.example.com.au</p>
  </section>

  <section class="card card--front" aria-label="Card front">
    <div class="front__top">
      <div class="brand">
        <div class="brand__row">
          <span class="brand__dot"></span>
          <span class="brand__name">CORVANE</span>
        </div>
        <span class="brand__sub">Electrical and Communications</span>
      </div>
    </div>

    <div class="front__band">
      <p class="person__name">BRENT MARLOW</p>
      <p class="person__title">PRESIDENT</p>
    </div>

    <div class="contacts">
      <p class="contacts__row">ABN: 71208349162 &nbsp;|&nbsp; Lic No: 418273D</p>
      <div class="contacts__row">
        <span class="contact">
          <svg viewBox="0 0 16 16" aria-hidden="true"><rect x="4" y="1" width="8" height="14" rx="1.5"/><rect x="5.5" y="3" width="5" height="8" fill="#f4f4f4"/></svg>
          0481209736
        </span>
        <span class="contact">
          <svg viewBox="0 0 16 16" aria-hidden="true"><rect x="1" y="3" width="14" height="10" rx="1"/><path d="M1.5 3.8 8 9 14.5 3.8" fill="none" stroke="#f4f4f4" stroke-width="1.3"/></svg>
          brent@corvaneelectricalandcomms.example.com.au
        </span>
      </div>
      <p class="contacts__row">
        <span class="contact">
          <svg viewBox="0 0 16 16" aria-hidden="true"><circle cx="8" cy="8" r="7"/><g fill="none" stroke="#f4f4f4" stroke-width="1"><ellipse cx="8" cy="8" rx="3" ry="7"/><path d="M1 8h14M2.5 4.5h11M2.5 11.5h11"/></g></svg>
          corvaneelectricalandcomms.example.com.au
        </span>
      </p>
    </div>
  </section>

</main>
</body>
</html>
```